Web Design Project

The aim of this project to design a website for a service that would offer services for small business and non profit organizations using opensource software that is weaved to work together in harmony.

The website name is: vestolia.net

Vestolia in Arabic means: cabbage. Cabbage is composed of leaves, actually there is nothing except leaves. Each leave by itself is not called cabbage, but a collection of leaves that are organized in a central way would give us cabbage.

Same idea for Vestolia where open source software very well organized and integrated would create a new thing with a new value.

Target Market(s)

Small business, Europe, Africa, Far east and Middle east

Industry/Entity Type

Small Business

Requirements
Must have
• The website would offer the following sections:
* Home page
* Benefits: value of vestolia
* Applications: applications offered by vestolia
* Pricing
* Purchase
* Customer log in
* Support
- FAQ
- Knowledge base
- Forums
- Open tickets

Please take the following consideration in design:
* White should predominate
* Only black and the colors of logo are permitted (attched)
Nice to have
• Design is better to express:
* Openness
* Dynamic
* Usable
* Cost effective

```html
<!DOCTYPE html>
<html lang="en">
<head>
<meta charset="utf-8">
<title>Vestolia — Home</title>
<link rel="stylesheet" href="https://fonts.googleapis.com/css2?family=Questrial&family=Open+Sans:wght@400;600;700&family=Fjalla+One&family=Arimo:wght@400&display=swap">
<style>
:root{
  --white:#ffffff;
  --ink:#1d1d1b;
  --dark-band:#333333;
  --blue:#0090dc;
  --yellow:#f7c300;
  --magenta:#b5508f;
  --green:#7dbd2c;
  --green-deep:#5f9b1c;
  --heading-grey:#7a6e66;
  --rule:#cfc8bf;
  --field:#f3f3f3;
  --field-border:#cfcfcf;
  --text-grey:#555555;
  --footer:#5b5b5b;
}
*{box-sizing:border-box;margin:0;padding:0}
html,body{width:1084px;height:1200px;overflow:hidden;background:var(--white)}
body{position:relative;font-family:"Open Sans",Arial,sans-serif;color:var(--ink)}
.abs{position:absolute}

/* header */
.brand{left:18px;top:40px;display:flex;align-items:center;gap:12px}
.brand-dot{width:34px;height:34px;border-radius:50%;background:var(--green)}
.brand-name{font-family:"Questrial",sans-serif;font-size:40px;color:var(--ink);line-height:1}
.account-links{right:30px;top:18px;display:flex;gap:12px}
.account-link{display:flex;flex-direction:column;align-items:center;font-family:Arimo,Arial,sans-serif;font-size:13px;color:var(--ink);gap:3px}
.account-link svg{width:20px;height:18px}
.tagline{right:29px;top:70px;font-family:"Questrial",sans-serif;font-size:29px;color:var(--ink)}

/* nav + hero */
.hero{left:0;top:120px;width:1084px;height:349px;background:var(--dark-band)}
.main-nav{left:18px;top:130px;display:flex;font-family:"Questrial",sans-serif;font-weight:700;font-size:19px;color:#dcdcdc}
.main-nav span{display:block;height:26px;line-height:26px;text-align:center;-webkit-text-stroke:.4px #dcdcdc}
.main-nav .current{background:var(--blue);color:var(--white);-webkit-text-stroke:.4px var(--white)}
.hero-title{left:45px;top:228px;font-family:"Questrial",sans-serif;font-size:35px;color:var(--white);-webkit-text-stroke:1px var(--white);letter-spacing:.3px}
.hero-copy{left:45px;top:279px;width:520px;font-size:15.5px;line-height:19px;color:var(--white)}
.btn-purchase{left:45px;top:373px;width:161px;height:36px;border-radius:4px;background:var(--green);font-family:"Questrial",sans-serif;font-weight:700;font-size:16px;line-height:36px;text-align:center;color:#243a0a;-webkit-text-stroke:.4px #243a0a}
.hero-visual{left:598px;top:182px;width:438px;height:336px;border-radius:14px 14px 30px 30px;background:linear-gradient(180deg,#4e5063 0%,#e6e6ea 70%,#a9a9ad 100%)}

/* feature cards */
.card{top:542px;width:333px;height:198px;color:var(--white);padding:26px 16px 0 16px;border-top:3px solid rgba(0,0,0,.08)}
.card--support{left:18px;background:var(--yellow)}
.card--apps{left:375px;background:var(--blue)}
.card--kb{left:729px;background:var(--magenta)}
.card-mark{position:absolute;right:18px;top:10px;width:80px;height:80px;border-radius:50%;background:rgba(255,255,255,.22)}
.card-title{position:relative;font-family:"Fjalla One",sans-serif;font-size:29px;line-height:32px;letter-spacing:-.3px}
.card-copy{position:relative;margin-top:8px;font-size:13.2px;line-height:16.5px}
.card-more{position:absolute;left:14px;top:144px;width:104px;height:27px;border-radius:14px;background:linear-gradient(#ffffff,#dcdcdc);box-shadow:0 1px 3px rgba(0,0,0,.3);font-family:"Open Sans",sans-serif;font-weight:700;font-size:10px;line-height:27px;text-align:center;color:#6a6a6a}

/* section heads */
.section-head{top:784px;width:336px;height:58px;border-top:4px solid #e4e0da;border-bottom:1px solid var(--rule);display:flex;align-items:center;gap:18px;padding-top:4px}
.section-head svg{width:30px;height:30px;flex:none}
.section-head h2{font-family:"Questrial",sans-serif;font-weight:400;font-size:27px;color:var(--heading-grey);letter-spacing:.5px}

/* contact form */
.field{left:12px;width:309px;background:var(--field);border:1px solid var(--field-border);border-radius:5px;font-size:13.5px;color:#444;padding:7px 12px}
.btn-send{left:13px;top:1038px;width:80px;height:27px;border-radius:14px;background:linear-gradient(#9bd454,var(--green-deep));font-weight:700;font-size:10px;line-height:27px;text-align:center;color:var(--white)}

/* news */
.news-item{left:374px;display:flex;gap:15px;width:335px}
.news-thumb{width:74px;height:74px;flex:none;border:1px solid #d8d8d8;padding:3px;background:var(--white)}
.news-thumb div{width:100%;height:100%}
.news-date{font-weight:700;font-size:16px;color:var(--blue);line-height:20px;margin-top:4px}
.news-copy{font-size:13.2px;line-height:16.2px;color:var(--text-grey);margin-top:3px}

/* testimonial */
.testimonial{left:763px;top:874px;width:300px;font-size:13.2px;line-height:16.2px;color:var(--text-grey)}
.testimonial p+p{margin-top:15px}
.testimonial-author{margin-top:14px;font-weight:700;color:var(--blue)}
.quote-mark{left:728px;top:930px;font-family:Georgia,serif;font-size:90px;line-height:1;color:#e3e8ef}

/* footer */
.footer-bar{left:0;top:1123px;width:1084px;height:28px;background:var(--footer)}
.footer-nav{left:0;top:1123px;width:1084px;height:28px;display:flex;justify-content:center;gap:0;font-family:Arimo,Arial,sans-serif;font-size:13px;line-height:28px;color:var(--white)}
.footer-nav span{padding:0 22px}
.legal{left:0;top:1161px;width:1084px;text-align:center;font-family:Arimo,Arial,sans-serif;font-size:12.5px;color:var(--ink);line-height:15px}
.legal small{display:block;font-size:12.5px;color:#555}
</style>
</head>
<body>

<header>
  <div class="abs brand"><span class="brand-dot"></span><span class="brand-name">vestolia</span></div>
  <nav class="abs account-links">
    <span class="account-link"><svg viewBox="0 0 20 18"><rect x="3" y="3" width="14" height="10" fill="#2b2b2b"/><rect x="1" y="13" width="18" height="2" fill="#2b2b2b"/></svg>login</span>
    <span class="account-link"><svg viewBox="0 0 20 18"><circle cx="10" cy="6" r="4.5" fill="#2b2b2b"/><path d="M3 18 Q10 8 17 18Z" fill="#2b2b2b"/></svg>support</span>
    <span class="account-link"><svg viewBox="0 0 20 18"><text x="10" y="15" text-anchor="middle" font-family="Arial" font-weight="700" font-size="16" fill="#2b2b2b">?</text></svg>FAQ</span>
  </nav>
  <p class="abs tagline">Creating a new thing with a new value</p>
</header>

<section class="abs hero"></section>
<nav class="abs main-nav">
  <span class="current" style="width:104px">home</span>
  <span style="width:125px">benefits</span>
  <span style="width:160px">applications</span>
  <span style="width:100px">pricing</span>
  <span style="width:133px">purchase</span>
  <span style="width:190px">knowledge base</span>
  <span style="width:155px">open tickets</span>
</nav>
<h1 class="abs hero-title">why use vestolia product?</h1>
<p class="abs hero-copy">Typi non habent claritatem insitam; est usus legentis in iis qui facit eorum claritatem. Investigationes demonstraverunt lectores legere me lius quod ii legunt saepius. Claritas est etiam processus dynamicus, qui sequitur mutationem consuetudium lectorum.</p>
<span class="abs btn-purchase">purchase product</span>
<div class="abs hero-visual" role="img" aria-label="Laptop showing the product dashboard with a colourful chart"></div>

<section class="abs card card--support">
  <span class="card-mark"></span>
  <h3 class="card-title">24/7 CLIENT SUPPORT</h3>
  <p class="card-copy">Lorem ipsum dolor sit amet, consectetuer adipiscing elit, sed diam nonummy nibh euismod tincidunt ut laoreet dolore magna.</p>
  <span class="card-more">READ MORE</span>
</section>
<section class="abs card card--apps">
  <span class="card-mark"></span>
  <h3 class="card-title">APPLICATIONS</h3>
  <p class="card-copy">Duis autem vel eum iriure dolor in hendrerit in vulputate velit esse molestie consequat, vel illum dolore eu feugiat nulla facilisis at vero eros.</p>
  <span class="card-more">READ MORE</span>
</section>
<section class="abs card card--kb">
  <span class="card-mark"></span>
  <h3 class="card-title">KNOWLEDGE BASE</h3>
  <p class="card-copy">Ut wisi enim ad minim veniam, quis nostrud exerci tation ullamcorper suscipit lobortis nisl ut aliquip ex ea commodo consequat.</p>
  <span class="card-more">READ MORE</span>
</section>

<div class="abs section-head" style="left:14px">
  <svg viewBox="0 0 30 30"><circle cx="15" cy="10" r="7" fill="#7a6e66"/><path d="M3 30 Q15 12 27 30Z" fill="#7a6e66"/><path d="M7 11 Q7 2 15 2 Q23 2 23 11" stroke="#7dbd2c" stroke-width="2" fill="none"/></svg>
  <h2>CONTACT US</h2>
</div>
<div class="abs section-head" style="left:373px">
  <svg viewBox="0 0 30 30"><rect x="3" y="5" width="24" height="23" rx="2" fill="none" stroke="#7a6e66" stroke-width="2.5"/><rect x="3" y="5" width="24" height="6" fill="#7a6e66"/><text x="15" y="25" text-anchor="middle" font-family="Arial" font-weight="700" font-size="11" fill="#7a6e66">15</text></svg>
  <h2>LATEST NEWS</h2>
</div>
<div class="abs section-head" style="left:728px">
  <svg viewBox="0 0 30 30"><ellipse cx="15" cy="13" rx="12" ry="9" fill="#7a6e66"/><path d="M8 19 L6 27 L14 21Z" fill="#7a6e66"/></svg>
  <h2>TESTIMONIALS</h2>
</div>

<form>
  <div class="abs field" style="top:876px;height:32px">Full Name</div>
  <div class="abs field" style="top:913px;height:32px">Email Address</div>
  <div class="abs field" style="top:950px;height:74px">Message</div>
  <span class="abs btn-send">SEND</span>
</form>

<article class="abs news-item" style="top:876px">
  <div class="news-thumb"><div role="img" aria-label="Green arrow graphic" style="background:linear-gradient(135deg,#eef3e4,#9fc86a)"></div></div>
  <div><p class="news-date">Fri, January. 03</p><p class="news-copy">Lorem ipsum dolor sit amet, consectet adipiscing elit, sed diam nonummy nibh euismod tincidunt ut .</p></div>
</article>
<article class="abs news-item" style="top:988px">
  <div class="news-thumb"><div role="img" aria-label="Blue globe graphic" style="background:linear-gradient(135deg,#cfeaf7,#3a9fd0)"></div></div>
  <div><p class="news-date">Mon, December. 28</p><p class="news-copy">Lorem ipsum dolor sit amet, consectet adipiscing elit, sed diam nonummy nibh euismod tincidunt ut .</p></div>
</article>

<span class="abs quote-mark">&ldquo;</span>
<blockquote class="abs testimonial">
  <p>Duis autem vel eum iriure dolor in hendrerit in vulputate velit esse molestie consequat, vel illum dolore eu feugiat nulla facilisis at vero eros et accumsan et iusto odio.</p>
  <p>Nam liber tempor cum soluta nobis eleifend option congue nihil imperdiet doming id quod mazim placerat facer possim assum.</p>
  <p class="testimonial-author">mr. Rolan Dastel (manager)</p>
</blockquote>

<footer>
  <div class="abs footer-bar"></div>
  <nav class="abs footer-nav">
    <span>home</span><span>benefits</span><span>applications</span><span>pricing</span><span>purchase</span><span>knowledge base</span><span>open tickets</span>
  </nav>
  <p class="abs legal">Privacy Policy | Terms of Use<small>Copyright 2014. All rights reserved.</small></p>
</footer>

</body>
</html>
```